BOLD & MINIMALIST DESIGN NEEDED

We want a very bold but minimalistic business card design that is impactful and utilizes both sides of the business card. Our current logo is included for your use.

We want bold fonts and good use of negative space. We don't want the logo to overpower the design.

Target Market(s)

Professionals who are building new commercial buildings.

Industry/Entity Type

Construction

Contact Information for Business Card

Name, Title, email, office phone, cell phone, website

Font styles to use
Serif
Sans Serif

Requirements
Must have
• Bold design!

```html
<!DOCTYPE html>
<html lang="en">
<head>
<meta charset="utf-8">
<title>Ridgecrest Design + Build – Business Card</title>
<link href="https://fonts.googleapis.com/css2?family=Montserrat:wght@500;600;700;800&display=swap" rel="stylesheet">
<style>
  :root {
    --stage: #ece8e2;
    --card-dark: #1a1a1a;
    --card-light: #ffffff;
    --ink: #151515;
    --accent: #8cc63f;
    --paper-text: #ffffff;
  }
  * { box-sizing: border-box; margin: 0; padding: 0; }
  html, body {
    width: 1200px;
    height: 1200px;
    overflow: hidden;
    background: var(--stage);
    font-family: "Montserrat", Arial, sans-serif;
  }
  .canvas { position: relative; width: 1200px; height: 1200px; }

  .card {
    position: absolute;
    left: 217px;
    width: 768px;
    height: 424px;
    border-radius: 24px;
    overflow: hidden;
    box-shadow: 0 8px 18px rgba(0,0,0,0.18);
  }
  .card--front { top: 159px; background: var(--card-dark); }
  .card--back  { top: 618px; background: var(--card-light); }

  /* Front: brand name */
  .front-brand {
    position: absolute;
    inset: 0;
    display: flex;
    align-items: center;
    justify-content: center;
    gap: 20px;
  }
  .front-brand__dot {
    width: 34px; height: 34px;
    border-radius: 50%;
    background: var(--accent);
  }
  .front-brand__name {
    color: var(--paper-text);
    font-weight: 800;
    font-size: 44px;
    letter-spacing: 1px;
    line-height: 1.1;
    text-transform: uppercase;
    text-align: left;
  }

  /* Back */
  .back-brand {
    position: absolute;
    left: 50px;
    top: 262px;
    width: 330px;
    display: flex;
    align-items: center;
    gap: 14px;
    transform: translateY(-150px);
  }
  .back-brand__dot {
    flex: none;
    width: 24px; height: 24px;
    border-radius: 50%;
    background: var(--accent);
  }
  .back-brand__name {
    color: var(--ink);
    font-weight: 800;
    font-size: 30px;
    line-height: 1.1;
    text-transform: uppercase;
  }
  .divider {
    position: absolute;
    left: 401px;
    top: 93px;
    width: 2px;
    height: 221px;
    background: var(--ink);
  }
  .contact {
    position: absolute;
    left: 441px;
    top: 88px;
    color: var(--ink);
  }
  .contact__name { font-weight: 700; font-size: 30px; line-height: 1.2; }
  .contact__title { font-weight: 500; font-size: 20px; margin-top: 6px; }
  .contact__list { list-style: none; margin-top: 36px; }
  .contact__item {
    display: flex;
    align-items: center;
    gap: 12px;
    font-weight: 500;
    font-size: 21px;
    height: 36px;
  }
  .contact__icon { width: 20px; height: 20px; flex: none; }

  .swoosh { position: absolute; left: 0; bottom: 0; width: 768px; height: 70px; }
</style>
</head>
<body>
<main class="canvas">

  <section class="card card--front" aria-label="Card front">
    <div class="front-brand">
      <span class="front-brand__dot"></span>
      <span class="front-brand__name">Ridgecrest<br>Design + Build</span>
    </div>
  </section>

  <section class="card card--back" aria-label="Card back">
    <div class="back-brand">
      <span class="back-brand__dot"></span>
      <span class="back-brand__name">Ridgecrest<br>Design + Build</span>
    </div>

    <div class="divider"></div>

    <div class="contact">
      <p class="contact__name">Marlon Keswick</p>
      <p class="contact__title">Founder &amp; CEO</p>
      <ul class="contact__list">
        <li class="contact__item">
          <svg class="contact__icon" viewBox="0 0 20 20"><path d="M2 8c0-3 4-5 8-5s8 2 8 5l-3 1-1-2H6L5 9z" fill="#8cc63f"/><rect x="4" y="10" width="12" height="7" rx="1.5" fill="#8cc63f"/></svg>
          <span>555-014-2200</span>
        </li>
        <li class="contact__item">
          <svg class="contact__icon" viewBox="0 0 20 20"><rect x="5" y="1.5" width="10" height="17" rx="2" fill="none" stroke="#8cc63f" stroke-width="1.8"/><circle cx="10" cy="15.5" r="1" fill="#8cc63f"/></svg>
          <span>555-014-2201</span>
        </li>
        <li class="contact__item">
          <svg class="contact__icon" viewBox="0 0 20 20"><rect x="1.5" y="4.5" width="17" height="11" fill="#8cc63f"/><path d="M1.5 4.5l8.5 6.5 8.5-6.5" fill="none" stroke="#fff" stroke-width="1.4"/></svg>
          <span>info@rcdb-build.com</span>
        </li>
        <li class="contact__item">
          <svg class="contact__icon" viewBox="0 0 20 20"><circle cx="10" cy="10" r="8.5" fill="#8cc63f"/><path d="M10 1.5v17M1.5 10h17M10 1.5c-4 4-4 13 0 17M10 1.5c4 4 4 13 0 17" fill="none" stroke="#fff" stroke-width="1"/></svg>
          <span>www.rcdb-build.com</span>
        </li>
      </ul>
    </div>

    <svg class="swoosh" viewBox="0 0 768 70" preserveAspectRatio="none" aria-hidden="true">
      <path d="M0 60 Q384 0 768 60" fill="none" stroke="var(--accent)" stroke-width="4"/>
      <path d="M0 70 L0 68 Q384 16 768 68 L768 70 Z" fill="var(--ink)"/>
      <path d="M0 70 Q384 22 768 70 Z" fill="var(--ink)"/>
    </svg>
  </section>

</main>
</body>
</html>
```